Bluefern Business Services needs a new interactive and interesting website

We need an interesting, professional, modern and functional company website for Bluefern Business Services - a young IT Services company based out of Chennai, India.

Bluefern Business Services is a fully owned subsidiary of Marlow Goods, one of the world's leading direct to consumer wine merchant.

We already have a registered company logo which must feature in the website.

We conceive, design, develop, test, implement and support IT solutions across the entire Marlow Goods IT landscape. For ex : We currently run about 25 e-commerce websites for Marlow Goods on ATG and Dot Net.

We would like to see our corporate colors used in the website. (Burgundy wine and wine green - source: www.bluefernbs-site.com)

We are looking at this website to communicate a fun, friendly and professionally managed company - reaching out to career seekers, prospective customers and general public.

For reference - The company name 'Bluefern' is an inspiration from the Marlow Goods lineage.

The second image with the world map is stickered on our main entrance to the office, I am not sure where this can be used -just putting it out there..

Please note that there are only a few more days to submit designs for this contest  !

I would appreciate if you can help posting your designs in time for our review and consideration.

Thanks.

Reason: Thanks for your inputs. We have a number of designers and a lot to digest and work with in the past few days. There has been a rush of new designs in the last few days Hence we will require more time to process these and make our decision. Hence i am requesting the contest to be open for more days. Regards, Tarun

Target Market(s)

Prospective job seekers who want to know more about the company and also wish to apply for a job vacancy
People wanting to know more about the company in general and our progress
People who want to see what we offer and how we can help them too - prospective customers
Companies that are interested in our IT Captive journey and are looking for a business opportunity

Industry/Entity Type

E-Commerce

Requirements
Must have
• Log In/ Register facility acting as a Single Sign on for Intranet (Employees)

Facility to post job vacancies (with an expiry date) and enable people to apply for a role and upload their CV/Resume.

Facility to Review Job applications

Facility for website visitors to contact Bluefern business Services via an online 'Contact Us' form with a split of job seekers and business opportunities

Gallery facility to upload pictures regarding company events
Nice to have
• Less Cluttered and contemporary design
Some Wine/Vineyard inspirations will be good but not too much, the company is an IT services company

```html
<!DOCTYPE html>
<html lang="en">
<head>
<meta charset="utf-8">
<title>Bluefern Business Services</title>
<link href="https://fonts.googleapis.com/css2?family=Open+Sans:wght@300;400;600&display=swap" rel="stylesheet">
<style>
:root{
  --burgundy:#8b0a3e;
  --wine-green:#7d8f2a;
  --wine-green-dark:#5f6e1c;
  --ink:#555;
  --muted:#888;
  --line:#ddd;
  --panel:#f2f2f2;
  --strip:#3b3b3b;
  --footer:#2e2e2e;
  --footer-deep:#1f1f1f;
}
*{box-sizing:border-box;margin:0;padding:0}
html,body{width:804px;height:1200px;overflow:hidden;background:#fff;font-family:"Open Sans",sans-serif;color:var(--ink)}
.page{position:relative;width:804px;height:1200px}
.abs{position:absolute}
.topbar{left:51px;top:0;width:704px;height:31px;background:var(--burgundy)}
.pill{top:5px;height:20px;background:#fff;border-radius:2px;font-size:8.5px;color:var(--burgundy);display:flex;align-items:center;gap:4px;padding:0 4px}
.brand{left:58px;top:44px}
.brand .mark{display:inline-block;width:20px;height:20px;border-radius:50%;background:var(--burgundy);vertical-align:middle;margin-right:4px}
.brand .name{font-size:27px;font-weight:600;color:var(--burgundy);vertical-align:middle;letter-spacing:-.5px}
.brand .sub{display:block;font-size:15px;color:var(--burgundy);margin-left:25px;margin-top:-4px}
.nav{top:62px;font-size:11px;color:#444;display:flex}
.nav a{text-decoration:none;color:#444;position:absolute;white-space:nowrap}
.nav a.active{color:var(--burgundy);font-weight:600}
.nav-bar{left:365px;top:100px;width:50px;height:3px;background:var(--burgundy)}
.strip{left:51px;top:103px;width:704px;height:33px;background:var(--strip)}
.social{top:114px;width:13px;height:13px;border-radius:2px;background:#2a74c4}
.hero{left:51px;top:136px;width:704px;height:307px;background:linear-gradient(110deg,#e9e6e1 0%,#b9b0a3 35%,#4b4a4f 55%,#23252d 80%,#50525a 100%)}
.arrow{top:277px;width:28px;height:28px;border-radius:50%;background:rgba(30,30,30,.75)}
.search{left:51px;top:443px;width:704px;height:44px;background:linear-gradient(#fafafa,#ececec);border:1px solid var(--line)}
.search .label{left:15px;top:13px;font-size:12px;color:#444}
.field{top:13px;height:20px;background:#fff;border:1px solid #ccc;font-size:10px;color:#888;padding:3px 7px}
.btn-search{left:610px;top:12px;width:68px;height:21px;background:var(--wine-green);border-radius:2px;color:#fff;font-size:9px;display:flex;align-items:center;gap:8px;padding-left:6px;box-shadow:0 2px 0 var(--wine-green-dark)}
.card{top:565px;width:145px;height:163px;background:var(--panel);border:1px solid var(--line);text-align:center;padding:20px 6px 0}
.card h3{font-size:10px;font-weight:400;color:#555;line-height:12px;white-space:nowrap}
.card p{font-size:7.5px;line-height:11.5px;color:#888;margin-top:8px;padding:0 4px}
.card .more{position:absolute;bottom:7px;left:50%;transform:translateX(-50%);background:var(--wine-green);color:#fff;font-size:7.5px;padding:2px 7px;white-space:nowrap}
.badge{top:519px;width:60px;height:60px;border-radius:50%;background:#fff;border:1px solid var(--wine-green);display:flex;align-items:center;justify-content:center}
.gallery{left:55px;top:766px;width:690px;height:194px;background:#f3f3f3}
.gallery h2{position:absolute;left:13px;top:13px;font-size:16px;font-weight:400;color:var(--burgundy)}
.gallery .upload{position:absolute;right:14px;top:17px;font-size:11px;color:#444;text-decoration:underline}
.shot{top:42px;width:151px;height:130px}
.footer{left:55px;top:963px;width:690px;height:227px;background:var(--footer);color:#fff}
.footer h4{position:absolute;top:22px;font-size:12.5px;font-weight:400}
.footer .text{position:absolute;font-size:8.5px;line-height:11.4px;color:#5f5f5f}
.copy{left:55px;top:1157px;width:690px;height:33px;background:var(--footer-deep);color:#ddd;font-size:7.5px;text-align:center;line-height:33px}
.map{left:528px;top:1022px;width:137px;height:114px;background:linear-gradient(135deg,#eceae2,#dcd9cc);border:1px solid #fff}
</style>
</head>
<body>
<div class="page">
  <div class="abs topbar"></div>
  <div class="abs pill" style="left:495px">
    <svg width="10" height="10" viewBox="0 0 10 10"><path d="M5 1 L9.5 5 H8 V9 H6 V6.5 H4 V9 H2 V5 H0.5 Z" fill="#666"/></svg>
    <span>B14 , Chennai, India 600041</span></div>
  <div class="abs pill" style="left:640px">
    <svg width="8" height="10" viewBox="0 0 8 10"><path d="M5 1 C2 1 1 3 1 5 C1 7 2 9 5 9" stroke="#666" stroke-width="1.6" fill="none"/></svg>
    <span>+91 (44) 55501234</span></div>

  <div class="abs brand"><span class="mark"></span><span class="name">bluefern</span><span class="sub">Business Services</span></div>
  <nav class="abs nav">
    <a class="active" style="left:374px">Home</a>
    <a style="left:439px">About Us</a>
    <a style="left:509px">Clients</a>
    <a style="left:572px">Services</a>
    <a style="left:636px">Careers</a>
    <a style="left:691px">Contact Us</a>
  </nav>
  <div class="abs nav-bar"></div>

  <div class="abs strip"></div>
  <div class="abs social" style="left:660px;background:#3b5998"></div>
  <div class="abs social" style="left:677px;background:#2aa3dd"></div>
  <div class="abs social" style="left:694px;background:#d9432f"></div>
  <div class="abs social" style="left:711px;background:#1da1dc"></div>
  <div class="abs social" style="left:728px;background:#1e6fd0"></div>

  <div class="abs hero" role="img" aria-label="Photo of two business colleagues reviewing work at a laptop"></div>
  <div class="abs arrow" style="left:75px"><svg width="28" height="28"><path d="M16 8 L10 14 L16 20" stroke="#fff" stroke-width="2" fill="none"/></svg></div>
  <div class="abs arrow" style="left:705px"><svg width="28" height="28"><path d="M12 8 L18 14 L12 20" stroke="#fff" stroke-width="2" fill="none"/></svg></div>

  <div class="abs search">
    <span class="abs label">I am looking for a</span>
    <div class="abs field" style="left:125px;width:155px">Job</div>
    <div class="abs" style="left:262px;top:13px;width:18px;height:20px;background:var(--wine-green)"><svg width="18" height="20"><path d="M5 8 L9 12 L13 8 Z" fill="#fff"/></svg></div>
    <span class="abs" style="left:293px;top:16px;font-size:10px;color:#555">In</span>
    <div class="abs field" style="left:316px;width:149px">Location</div>
    <div class="abs field" style="left:474px;width:122px">Industry/Role</div>
    <div class="abs btn-search"><svg width="10" height="10"><circle cx="4" cy="4" r="3" stroke="#fff" stroke-width="1.3" fill="none"/><path d="M6 6 L9 9" stroke="#fff" stroke-width="1.5"/></svg>Search</div>
  </div>

  <div class="abs card" style="left:55px"><h3>Packaged Applications</h3><p>Lorem Ipsum is simply dummy text of the printing and typesetting industry. Lorem Ipsum has been the industry's standard dummy text ever since the 1500s, when an unknown printer took a galley</p><span class="more">Read More</span></div>
  <div class="abs card" style="left:240px"><h3>Digital Commerce</h3><p>Lorem Ipsum is simply dummy text of the printing and typesetting industry. Lorem Ipsum has been the industry's standard dummy text ever since the 1500s, when an unknown printer took a galley</p><span class="more">Read More</span></div>
  <div class="abs card" style="left:420px"><h3>Enterprises Application<br>Integration</h3><p>Lorem Ipsum is simply dummy text of the printing and typesetting industry. Lorem Ipsum has been the industry's standard dummy text ever since the 1500s,</p><span class="more">Read More</span></div>
  <div class="abs card" style="left:601px"><h3>Application Development<br>&amp; Maintenance</h3><p>Lorem Ipsum is simply dummy text of the printing and typesetting industry. Lorem Ipsum has been the industry's standard dummy text ever since the 1500s,</p><span class="more">Read More</span></div>

  <div class="abs badge" style="left:97px"><svg width="28" height="26" viewBox="0 0 28 26"><rect x="2" y="2" width="24" height="16" rx="1" fill="none" stroke="var(--burgundy)" stroke-width="2.5"/><path d="M7 7 H21 M7 11 H17" stroke="var(--burgundy)" stroke-width="2"/><path d="M11 18 V22 H17 V18 M8 23 H20" stroke="var(--burgundy)" stroke-width="2.5" fill="none"/></svg></div>
  <div class="abs badge" style="left:282px"><svg width="30" height="24" viewBox="0 0 30 24"><path d="M2 3 Q8 1 14 4 V22 Q8 19 2 21 Z M28 3 Q22 1 16 4 V22 Q22 19 28 21 Z" fill="var(--burgundy)"/><path d="M5 7 H11 M5 11 H11 M19 7 H25 M19 11 H25" stroke="#fff" stroke-width="1.3"/></svg></div>
  <div class="abs badge" style="left:462px"><svg width="30" height="30" viewBox="0 0 30 30"><g fill="var(--burgundy)"><circle cx="15" cy="15" r="9"/><rect x="13" y="1" width="4" height="6"/><rect x="13" y="23" width="4" height="6"/><rect x="1" y="13" width="6" height="4"/><rect x="23" y="13" width="6" height="4"/><rect x="13" y="1" width="4" height="6" transform="rotate(45 15 15)"/><rect x="13" y="23" width="4" height="6" transform="rotate(45 15 15)"/><rect x="1" y="13" width="6" height="4" transform="rotate(45 15 15)"/><rect x="23" y="13" width="6" height="4" transform="rotate(45 15 15)"/></g><circle cx="15" cy="15" r="4" fill="#fff"/></svg></div>
  <div class="abs badge" style="left:643px"><svg width="30" height="30" viewBox="0 0 30 30" fill="none" stroke="var(--burgundy)" stroke-width="2"><circle cx="15" cy="15" r="13"/><ellipse cx="15" cy="15" rx="6" ry="13"/><path d="M2 15 H28 M4 8 H26 M4 22 H26 M15 2 V28"/></svg></div>

  <section class="abs gallery">
    <h2>Gallery</h2><span class="upload">Upload Picture</span>
    <div class="abs shot" style="left:13px;background:linear-gradient(135deg,#4a5a6e,#c9ced6 60%,#e8e9ec)" role="img" aria-label="Photo of a business handshake"></div>
    <div class="abs shot" style="left:182px;background:linear-gradient(160deg,#f2f2f2,#9aa7b1 55%,#cfe0e3)" role="img" aria-label="Photo of a team meeting around a table"></div>
    <div class="abs shot" style="left:356px;background:linear-gradient(135deg,#2c5e92,#8fb3d6 50%,#1f4b7a)" role="img" aria-label="Close photo of a circuit board"></div>
    <div class="abs shot" style="left:526px;background:linear-gradient(135deg,#e7ebef,#b7c2cc 50%,#d9c6b7)" role="img" aria-label="Photo of hands typing on a laptop"></div>
    <div class="abs" style="left:13px;top:84px;width:18px;height:46px;background:rgba(40,40,40,.45)"><svg width="18" height="46"><path d="M11 18 L7 23 L11 28" stroke="#fff" fill="none"/></svg></div>
    <div class="abs" style="left:659px;top:84px;width:18px;height:46px;background:rgba(40,40,40,.45)"><svg width="18" height="46"><path d="M7 18 L11 23 L7 28" stroke="#fff" fill="none"/></svg></div>
  </section>

  <footer class="abs footer">
    <div style="position:absolute;left:26px;top:18px"><span style="display:inline-block;width:14px;height:14px;border-radius:50%;background:#fff;vertical-align:middle;margin-right:3px"></span><span style="font-size:20px;font-weight:600;vertical-align:middle">bluefern</span><span style="display:block;font-size:11px;margin-left:17px">Business Services</span></div>
    <p class="text" style="left:26px;top:71px;width:140px">Here at Bluefern Business Services we're always happy to hear from you!</p>
    <h4 style="left:205px">Contact Info</h4>
    <p class="text" style="left:205px;top:57px">Bluefern Business Services Pvt. Ltd.<br>4th Floor, Harbor View Tower II<br>Unit B14 Lakeside Industrial Estate<br>Velmur<br>Chennai, 600041<br>Tamil Nadu<br><br>Tel: +91 (44) 55501234<br><br>Email: hello@bluefernbs-site.com</p>
    <h4 style="left:402px">Navigation</h4>
    <p class="text" style="left:404px;top:56px">Home<br>About Us<br>Clients<br>Services<br>Careers<br>Contact Us</p>
    <h4 style="left:527px">Find Us</h4>
  </footer>
  <div class="abs map" role="img" aria-label="Street map showing the office location"></div>
  <div class="abs copy">Copyright Bluefern Business Services Private Limited</div>
</div>
</body>
</html>
```